Marlowby Services Website Design

We have most content but require a professional design. We have a logo already and will need it utilized along with several of the photos from the attached documentation.
First page should have our mission and Vision and the synapsis provided in the word document. Visitors will be prompted to select from one of our 3 divisions from this page.
Each division will have the same list of tabs : About, Services, Safety, Careers and Contact.
Photos on each divisions page should be representative of the divisions offerings. The word doc attached contains the requested content and we are open to edits that would complement and fill the website.
I like the Quorvane site www.quorvane.example - they are our competition so cant be modeled directly after this.
Please include prompts to request quote at each service page. align the format of the geotechnical page to the other 2 divisions.
I used chat gpt for some of the content so will need it optimized for SCO.

```html
<!DOCTYPE html>
<html lang="en">
<head>
<meta charset="utf-8">
<title>Marlowby Services</title>
<link href="https://fonts.googleapis.com/css2?family=Orbitron:wght@600;700;800&family=Lato:wght@400;700&display=swap" rel="stylesheet">
<style>
:root{
  --red:#e81f27;
  --white:#ffffff;
  --ink:#1d1d1d;
  --night:#0b0b0b;
  --line:#8a8a8a;
}
*{margin:0;padding:0;box-sizing:border-box}
html,body{width:1200px;height:3223px;overflow:hidden;background:var(--white)}
body{position:relative;font-family:"Lato",sans-serif;color:var(--ink)}
.display{font-family:"Orbitron",sans-serif;font-weight:700;letter-spacing:1px;text-transform:uppercase}

/* hero */
.hero{position:absolute;left:0;top:0;width:1200px;height:647px;
  background:linear-gradient(180deg,#16233a 0%,#2c4668 28%,#4c5a55 42%,#6b5a44 55%,#8d7458 75%,#9a8064 100%)}
.hero-truck{position:absolute;left:60px;top:340px;width:1020px;height:307px;
  background:linear-gradient(180deg,#e9ecef 0%,#cfd4d8 55%,#5b5e60 100%);border-radius:8px 8px 0 0;opacity:.85}
.brand{position:absolute;left:70px;top:34px;font-family:"Orbitron",sans-serif;font-weight:800;font-size:38px;letter-spacing:2px;color:var(--white)}
.nav{position:absolute;top:47px;font-family:"Orbitron",sans-serif;font-weight:700;font-size:13px;color:var(--white)}
.nav a{position:absolute;color:inherit;text-decoration:none;white-space:nowrap}
.btn{position:absolute;display:flex;align-items:center;justify-content:center;font-family:"Orbitron",sans-serif;font-weight:700;font-size:14px;text-transform:uppercase;letter-spacing:.5px;transform:skewX(-8deg)}
.btn span{transform:skewX(8deg)}
.btn-light{background:var(--white);color:var(--red);box-shadow:5px 4px 0 var(--red)}
.btn-red{background:var(--red);color:var(--white);box-shadow:5px 4px 0 var(--ink)}
.hero-title{position:absolute;left:0;width:1200px;top:176px;text-align:center;color:var(--white);font-size:48px;font-weight:800;text-shadow:0 3px 8px rgba(0,0,0,.5)}

.section-title{position:absolute;left:0;width:1200px;text-align:center;color:var(--red);font-size:35px;font-weight:800}

/* tiles */
.tile{position:absolute;clip-path:polygon(6% 0,100% 0,94% 100%,0 100%)}
.tile .photo{position:absolute;left:0;top:0;width:100%}
.tile .label{position:absolute;left:0;bottom:0;width:100%;height:46px;background:var(--red);color:var(--white);display:flex;align-items:center;justify-content:center;font-family:"Orbitron",sans-serif;font-weight:700;font-size:14px;letter-spacing:.5px}

.block-photo{position:absolute}
.block-title{position:absolute;color:var(--red);font-size:35px;font-weight:800}
.block-text{position:absolute;font-size:15px;line-height:29px;color:#222}

.arrow{position:absolute;width:30px;height:30px}

/* footer */
.footer{position:absolute;left:0;top:2630px;width:1200px;height:593px;background:var(--night);color:var(--white)}
.field{position:absolute;top:95px;height:50px;border:1px solid #cfcfcf;border-radius:2px;font-size:13px;padding-left:16px;display:flex;align-items:center;font-family:Arial,sans-serif}
.subscribe{position:absolute;top:95px;left:913px;width:173px;height:50px;background:var(--red);display:flex;align-items:center;justify-content:center;font-family:Arial,sans-serif;font-weight:700;font-size:13px}
.rule{position:absolute;left:111px;width:977px;height:1px;background:var(--line)}
.foot-brand{position:absolute;left:111px;top:236px;font-family:"Orbitron",sans-serif;font-weight:800;font-size:30px;letter-spacing:2px;color:var(--red)}
.social{position:absolute;top:305px;width:30px;height:30px;border-radius:50%;background:#2a2a2a;border:1px solid #555}
.col-title{position:absolute;top:238px;font-family:"Orbitron",sans-serif;font-weight:700;font-size:17px;letter-spacing:.5px}
.links{position:absolute;top:280px;list-style:none;font-size:15px}
.links li{height:34.5px;display:flex;align-items:center}
.links li::before{content:"»";font-size:16px;margin-right:14px}
.contact-row{position:absolute;left:886px;display:flex;align-items:center;font-size:15px;line-height:25px;white-space:nowrap}
.contact-row .ico{width:28px;height:28px;border-radius:50%;background:#262626;display:flex;align-items:center;justify-content:center;margin-right:14px;flex:none}
.copyright{position:absolute;left:0;width:1200px;top:542px;text-align:center;font-size:15px}
</style>
</head>
<body>

<header class="hero">
  <div class="hero-truck" role="img" aria-label="Photo of a white boom truck with an aerial lift parked on a gravel lot"></div>
  <div class="brand">MARLOWBY</div>
  <nav class="nav">
    <a style="left:479px">ABOUT</a>
    <a style="left:594px">SERVICES</a>
    <a style="left:732px">SAFETY</a>
    <a style="left:856px">CAREERS</a>
  </nav>
  <div class="btn btn-light" style="left:978px;top:34px;width:148px;height:43px"><span>Contact Us</span></div>
  <h1 class="hero-title display">Welcome to Marlowby</h1>
  <div class="btn btn-light" style="left:517px;top:264px;width:164px;height:45px"><span>Get Started</span></div>
</header>

<h2 class="section-title display" style="top:693px">Select Division</h2>

<div class="tile" style="left:125px;top:760px;width:307px;height:332px">
  <div class="photo" role="img" aria-label="Photo of a crane boom beside a water tower" style="height:286px;background:linear-gradient(180deg,#3f78c4 0%,#8fb2d8 65%,#7a7a60 100%)"></div>
  <div class="label">AERIAL ACCESS</div>
</div>
<div class="tile" style="left:447px;top:760px;width:308px;height:332px">
  <div class="photo" role="img" aria-label="Aerial photo of a drilling truck on dry ground" style="height:286px;background:linear-gradient(135deg,#8a7656 0%,#6e5e44 50%,#cfcfcf 100%)"></div>
  <div class="label">GEOTECHNICAL DRILLING</div>
</div>
<div class="tile" style="left:768px;top:760px;width:307px;height:332px">
  <div class="photo" role="img" aria-label="Photo of solar panels under a blue sky" style="height:286px;background:linear-gradient(160deg,#2d7be0 0%,#1b4fb0 50%,#0e2c7a 100%)"></div>
  <div class="label">RENEWABLE ENERGY</div>
</div>

<div class="block-photo" role="img" aria-label="Aerial photo of a lift basket above a small town" style="left:600px;top:1164px;width:489px;height:454px;background:linear-gradient(180deg,#c9ccc9 0%,#6f7a6b 35%,#4d5548 70%,#8a8d86 100%)"></div>
<h2 class="block-title display" style="left:111px;top:1268px">Our Vision</h2>
<p class="block-text" style="left:111px;top:1335px;width:450px">To be the leading provider of aerial access, geotechnical drilling, and service solutions, setting the standard for excellence in safety, efficiency, and environmental stewardship.</p>
<div class="btn btn-red" style="left:115px;top:1455px;width:166px;height:45px"><span>Read More</span></div>

<div class="block-photo" role="img" aria-label="Overhead photo of a white boom truck" style="left:111px;top:1618px;width:489px;height:453px;background:linear-gradient(180deg,#8c7d64 0%,#e6e8ea 12%,#d2d5d8 45%,#6b6f72 62%,#76664f 78%,#6a5a44 100%)"></div>
<h2 class="block-title display" style="left:668px;top:1685px">Our Mission</h2>
<p class="block-text" style="left:668px;top:1744px;width:425px">At Marlowby, our mission is to deliver unparalleled aerial access, geotechnical drilling, and service and maintenance solutions, consistently exceeding our clients' expectations. We strive to achieve this by investing in cutting-edge technology, fostering a culture of safety and continuous improvement, and prioritizing environmental sustainability.</p>
<div class="btn btn-red" style="left:672px;top:1942px;width:166px;height:45px"><span>Read More</span></div>

<h2 class="section-title display" style="top:2149px">Our Services</h2>

<svg class="arrow" style="left:37px;top:2374px" viewBox="0 0 30 30" aria-hidden="true"><circle cx="15" cy="15" r="13" fill="none" stroke="#e81f27" stroke-width="3"/><path d="M21 15H10M15 9l-6 6 6 6" fill="none" stroke="#e81f27" stroke-width="3.5" stroke-linecap="round" stroke-linejoin="round"/></svg>
<svg class="arrow" style="left:1137px;top:2374px" viewBox="0 0 30 30" aria-hidden="true"><circle cx="15" cy="15" r="13" fill="none" stroke="#e81f27" stroke-width="3"/><path d="M9 15h11M15 9l6 6-6 6" fill="none" stroke="#e81f27" stroke-width="3.5" stroke-linecap="round" stroke-linejoin="round"/></svg>

<div class="tile" style="left:111px;top:2224px;width:308px;height:332px">
  <div class="photo" role="img" aria-label="Photo of a hand holding a phone over a clipboard" style="height:286px;background:linear-gradient(135deg,#f1efec 0%,#d9d3cc 50%,#3d4f8f 80%,#4a3428 100%)"></div>
  <div class="label">DELIVERING SAFE</div>
</div>
<div class="tile" style="left:444px;top:2224px;width:307px;height:332px">
  <div class="photo" role="img" aria-label="Aerial photo of a lift basket with a sign over a town" style="height:286px;background:linear-gradient(180deg,#8a9096 0%,#b7babd 40%,#5d6468 100%)"></div>
  <div class="label">RELIABLE AERIAL ACCESS</div>
</div>
<div class="tile" style="left:780px;top:2224px;width:306px;height:332px">
  <div class="photo" role="img" aria-label="Photo of a refinery with pipelines at sunset" style="height:286px;background:linear-gradient(180deg,#3a6f9a 0%,#c77a45 45%,#f4a23a 60%,#7a2a20 100%)"></div>
  <div class="label">OIL&amp;GAS</div>
</div>

<footer class="footer">
  <div class="field" style="left:111px;width:181px">First Name:</div>
  <div class="field" style="left:310px;width:181px">Email:</div>
  <div class="field" style="left:510px;width:181px">Phone:</div>
  <div class="field" style="left:712px;width:181px">Address:</div>
  <div class="subscribe">SUBSCREIBE</div>

  <div class="rule" style="top:199px"></div>

  <div class="foot-brand">MARLOWBY</div>
  <div class="social" style="left:110px"></div>
  <div class="social" style="left:168px"></div>
  <div class="social" style="left:226px"></div>
  <div class="social" style="left:284px"></div>

  <div class="col-title" style="left:413px">QUICK LINKS</div>
  <ul class="links" style="left:413px">
    <li>Home</li><li>About Us</li><li>Services</li><li>Safety</li><li>Contact Us</li>
  </ul>

  <div class="col-title" style="left:648px">OTHER LINKS</div>
  <ul class="links" style="left:648px">
    <li>FAQ</li><li>Careers</li><li>Privacy Policy</li><li>Returns Policy</li><li>Terms of use</li>
  </ul>

  <div class="col-title" style="left:886px">CONTACT US</div>
  <div class="contact-row" style="top:283px">
    <span class="ico"><svg width="13" height="13" viewBox="0 0 24 24"><path d="M6.6 10.8a15 15 0 0 0 6.6 6.6l2.2-2.2c.3-.3.7-.4 1-.2 1.1.4 2.3.6 3.6.6.6 0 1 .4 1 1V20c0 .6-.4 1-1 1A17 17 0 0 1 3 4c0-.6.4-1 1-1h3.5c.6 0 1 .4 1 1 0 1.3.2 2.5.6 3.6.1.3 0 .7-.2 1z" fill="#fff"/></svg></span>
    +1 555 014 2290
  </div>
  <div class="contact-row" style="top:348px">
    <span class="ico"><svg width="14" height="12" viewBox="0 0 24 20"><rect x="2" y="2" width="20" height="16" rx="2" fill="none" stroke="#fff" stroke-width="2"/><path d="M2 4l10 7 10-7" fill="none" stroke="#fff" stroke-width="2"/></svg></span>
    info@marlowby.example
  </div>
  <div class="contact-row" style="top:400px">
    <span class="ico"><svg width="11" height="14" viewBox="0 0 20 26"><path d="M10 0a9 9 0 0 0-9 9c0 7 9 17 9 17s9-10 9-17a9 9 0 0 0-9-9zm0 12a3 3 0 1 1 0-6 3 3 0 0 1 0 6z" fill="#fff"/></svg></span>
    <span>Marlowby<br>United States</span>
  </div>

  <div class="rule" style="top:511px"></div>
  <div class="copyright">Copyrights@2024.Marlowby.All Rights Reserved</div>
</footer>

</body>
</html>
```